Business is called "Keel Ledger". Accounting and tax services.

I need a flyer for my new business "Keel Ledger". I am an individual accountant working for himself on the Sunshine Coast in Queensland Australia. I would like to see designs that communicate reliability and trust. I believe my point of difference is that I am always available to my clients and I will cap my number of clients to ensure I can service them properly. Accountants in general seem to have a bad reputation for not responding to clients in a timely fashion, whether by email or phone. This is where I intend to differentiate myself. I have included my business card for ideas on colour and for contact information. I have also included some logo's that should go on the flyer. With the RFN logo, the words "Keel Ledger is a RFN Business" needs to be written either above, below or to the right hand side (as per the business card).

Target Market(s)

Small business owners and individuals requiring taxation and financials

Industry/Entity Type

Public Accounting

Font styles to use
Serif

Requirements
Must have
• Supplied logo's, accounting style pictures etc
Services: Small Business Taxation
Company & Trust Tax Returns
Rental Property Returns
Capital Gains Tax
Individual Tax Returns
BAS and IAS lodgements
Nice to have
• Needs to convey a sense of being reliable and responds to clients quickly.
Should not have
• My name

```html
<!DOCTYPE html>
<html lang="en">
<head>
<meta charset="utf-8">
<title>Keel Ledger – Accounting &amp; Tax Flyer</title>
<link href="https://fonts.googleapis.com/css2?family=Montserrat:wght@400;500;600;700;800&display=swap" rel="stylesheet">
<style>
  :root{
    --teal:#1fae8c;
    --teal-mid:#45bf9f;
    --teal-light:#7ed2bb;
    --teal-glass:rgba(38,190,150,0.82);
    --ink:#1f2a30;
    --muted:#8a949a;
    --paper:#ffffff;
    --sky-top:#c9d3dc;
    --sky-bottom:#3c4a57;
    --rule:#d6dbde;
  }
  *{margin:0;padding:0;box-sizing:border-box}
  html,body{width:857px;height:1200px;overflow:hidden;background:var(--paper)}
  body{font-family:"Montserrat",Arial,sans-serif;color:var(--ink)}

  .flyer{position:relative;width:857px;height:1200px;background:var(--paper)}

  .hero{position:absolute;left:0;top:0;width:857px;height:620px}
  .hero-photo{position:absolute;inset:0;
    background:linear-gradient(160deg,var(--sky-top) 0%,#9aa8b5 40%,#5b6a78 70%,var(--sky-bottom) 100%)}

  .headline-box{position:absolute;left:0;top:0;width:490px;height:232px;
    background:var(--teal-glass);padding:58px 40px 0 58px}
  .headline{color:#fff;font-weight:800;font-size:31px;line-height:1.3;letter-spacing:.5px;text-transform:uppercase}
  .headline-rule{width:60px;height:4px;background:#fff;margin-top:18px}

  .promise-box{position:absolute;left:560px;top:240px;width:225px;height:205px;
    background:var(--paper);padding:28px 22px 0 22px}
  .promise-icon{width:36px;height:30px;display:block;margin-bottom:14px}
  .promise{font-weight:800;font-size:18px;line-height:1.3;text-transform:uppercase;color:var(--ink)}

  .services{position:absolute;left:0;top:655px;width:857px}
  .services-title{text-align:center;font-weight:700;font-size:22px;letter-spacing:.5px;text-transform:uppercase}
  .services-rule{width:56px;height:3px;background:var(--teal);margin:10px auto 0}
  .service-grid{display:grid;grid-template-columns:repeat(3,1fr);margin-top:30px}
  .service{height:76px;display:flex;align-items:center;justify-content:center;text-align:center;
    color:#fff;font-weight:700;font-size:14px;line-height:1.35;letter-spacing:.4px;text-transform:uppercase;padding:0 20px}
  .service.tone-a{background:var(--teal)}
  .service.tone-b{background:var(--teal-mid)}
  .service.tone-c{background:var(--teal-light)}

  .stats{position:absolute;left:0;top:935px;width:857px;text-align:center;
    color:var(--muted);font-size:13px;font-weight:600;letter-spacing:1px;text-transform:uppercase}
  .stats span{margin:0 12px}

  .footer{position:absolute;left:58px;right:58px;top:1000px;height:120px;display:flex;align-items:center}
  .brand{display:flex;flex-direction:column;align-items:center;width:150px}
  .brand-mark{width:42px;height:42px;border-radius:50%;border:2px solid var(--ink);margin-bottom:10px}
  .brand-name{font-weight:600;font-size:18px;letter-spacing:3px;text-transform:uppercase;color:var(--ink)}
  .divider{width:1px;height:90px;background:var(--rule);margin:0 34px}
  .partners{display:flex;align-items:center;gap:26px}
  .partner{display:flex;flex-direction:column;align-items:center;gap:6px}
  .badge-rect{width:58px;height:26px;background:#2c4f86}
  .badge-round{width:40px;height:40px;border-radius:50%;background:#f2c230}
  .badge-dot{width:40px;height:40px;border-radius:50%;background:#2f9be0}
  .partner-note{font-size:9px;color:var(--muted);font-weight:500;white-space:nowrap}
  .contact{margin-left:auto;text-align:right;font-size:13px;line-height:1.7;color:var(--teal);font-weight:500}
</style>
</head>
<body>
  <main class="flyer">
    <section class="hero">
      <div class="hero-photo" role="img" aria-label="Photograph looking up at glass city office towers against a pale sky"></div>
      <div class="headline-box">
        <h1 class="headline">We do the numbers and help your business grow</h1>
        <div class="headline-rule"></div>
      </div>
      <div class="promise-box">
        <svg class="promise-icon" viewBox="0 0 36 30" aria-hidden="true">
          <polygon points="0,0 36,15 0,30 8,15" fill="#2f9be0"/>
        </svg>
        <p class="promise">Our speciality is reliability &amp; super fast communication</p>
      </div>
    </section>

    <section class="services">
      <h2 class="services-title">Our Services</h2>
      <div class="services-rule"></div>
      <div class="service-grid">
        <div class="service tone-a">Small Business<br>Taxation</div>
        <div class="service tone-a">Company &amp; Trust<br>Tax Returns</div>
        <div class="service tone-b">Rental Property<br>Returns</div>
        <div class="service tone-c">Capital Gain<br>Tax</div>
        <div class="service tone-b">Individual Tax<br>Returns</div>
        <div class="service tone-a">BAS and IAS<br>Lodgement</div>
      </div>
    </section>

    <p class="stats"><span>50+ Clients</span>|<span>15+ Years of Experience</span>|<span>24 Hrs Support</span></p>

    <footer class="footer">
      <div class="brand">
        <div class="brand-mark"></div>
        <div class="brand-name">Keel Ledger</div>
      </div>
      <div class="divider"></div>
      <div class="partners">
        <div class="partner">
          <div class="badge-rect"></div>
          <div class="partner-note">Keel Ledger is a RFN Business</div>
        </div>
        <div class="partner"><div class="badge-round"></div></div>
        <div class="partner"><div class="badge-dot"></div></div>
      </div>
      <div class="contact">
        <div>07 5550 1234</div>
        <div>hello@keelledger.com.au</div>
      </div>
    </footer>
  </main>
</body>
</html>
```